Ridgeline Journeys business card

please see website
www.ridgelinejourneys.comau

info needed on card
Curtis Halvey
Ph
email
Adventure Riding GPS trails

please use my logo and colours off my site

Curtis Halvey
curtis@ridgelinejourneys.com

```html
<!DOCTYPE html>
<html lang="en">
<head>
<meta charset="utf-8">
<title>Ridgeline Journeys – Business Card</title>
<link rel="stylesheet" href="https://fonts.googleapis.com/css2?family=Open+Sans:ital,wght@0,400;0,600;0,800;1,700&display=swap">
<style>
  :root {
    --backdrop: #2e3034;
    --brand-yellow: #ffd20a;
    --brand-yellow-light: #ffe24d;
    --card-white: #ffffff;
    --ink: #111111;
    --rule-yellow: #f5d21e;
  }
  * { box-sizing: border-box; margin: 0; padding: 0; }
  html, body {
    width: 1200px; height: 864px; overflow: hidden;
    background: var(--backdrop);
    font-family: "Open Sans", Arial, sans-serif;
  }
  .stage {
    width: 1200px; height: 864px;
    display: flex; flex-direction: column; align-items: center; justify-content: center;
    gap: 40px;
  }
  .card {
    position: relative;
    width: 600px; height: 343px;
    border-radius: 3px;
    overflow: hidden;
  }

  /* Front */
  .card--front {
    background: radial-gradient(circle at 52% 38%, var(--brand-yellow-light) 0%, var(--brand-yellow) 55%, #f9cc00 100%);
  }
  .front__name {
    position: absolute; left: 0; right: 0; top: 70px;
    text-align: center;
    color: #ffffff;
    font-weight: 800;
    text-transform: uppercase;
    line-height: 1.0;
  }
  .front__name-line1 { display: block; font-size: 46px; letter-spacing: 1px; }
  .front__name-line2 { display: block; font-size: 58px; letter-spacing: 1px; }
  .front__rule {
    position: absolute; left: 0; right: 0; top: 262px;
    height: 1px; background: rgba(255,255,255,0.85);
  }
  .front__web {
    position: absolute; left: 0; right: 0; top: 252px;
    text-align: center;
  }
  .front__web span {
    background: var(--brand-yellow);
    padding: 0 10px;
    color: #ffffff; font-size: 13px; font-weight: 600;
  }

  /* Back */
  .card--back {
    background: linear-gradient(160deg, #ffffff 0%, #f3f3f3 100%);
  }
  .back__brand {
    position: absolute; left: 0; right: 0; top: 42px;
    display: flex; align-items: center; justify-content: center; gap: 22px;
  }
  .back__mark {
    width: 74px; height: 74px;
    background: var(--brand-yellow);
  }
  .back__name {
    color: var(--ink);
    font-weight: 800;
    text-transform: uppercase;
    line-height: 1.0;
  }
  .back__name-line1 { display: block; font-size: 30px; }
  .back__name-line2 { display: block; font-size: 38px; }
  .back__tagline {
    position: absolute; left: 0; right: 0; top: 136px;
    text-align: center;
    color: var(--ink);
    font-size: 13px; font-weight: 700; font-style: italic;
    letter-spacing: 0.3px; text-transform: uppercase;
  }
  .back__rule {
    position: absolute; left: 0; right: 0; top: 190px;
    height: 1px; background: var(--rule-yellow);
  }
  .back__person {
    position: absolute; left: 0; right: 0; top: 179px;
    text-align: center;
  }
  .back__person span {
    background: #f9f9f9;
    padding: 0 10px;
    color: var(--brand-yellow);
    font-size: 16px; font-weight: 600;
  }
  .back__contacts {
    position: absolute; left: 0; right: 0; top: 216px;
    list-style: none;
    display: flex; flex-direction: column; align-items: center; gap: 4px;
    color: var(--ink); font-size: 14px;
  }
  .contact { display: flex; align-items: center; gap: 6px; }
  .contact svg { width: 12px; height: 12px; fill: var(--brand-yellow); }
</style>
</head>
<body>
<main class="stage">

  <section class="card card--front" aria-label="Card front">
    <h1 class="front__name">
      <span class="front__name-line1">Ridgeline</span>
      <span class="front__name-line2">Journeys</span>
    </h1>
    <div class="front__rule"></div>
    <p class="front__web"><span>www.ridgelinejourneys.com</span></p>
  </section>

  <section class="card card--back" aria-label="Card back">
    <div class="back__brand">
      <div class="back__mark"></div>
      <h2 class="back__name">
        <span class="back__name-line1">Ridgeline</span>
        <span class="back__name-line2">Journeys</span>
      </h2>
    </div>
    <p class="back__tagline">Adventure Riding GPS Trails</p>
    <div class="back__rule"></div>
    <p class="back__person"><span>Curtis Halvey</span></p>
    <ul class="back__contacts">
      <li class="contact">
        <svg viewBox="0 0 24 24" aria-hidden="true"><path d="M6.6 10.8a15.1 15.1 0 0 0 6.6 6.6l2.2-2.2c.3-.3.7-.4 1-.2 1.1.4 2.3.6 3.6.6.6 0 1 .4 1 1V20c0 .6-.4 1-1 1A17 17 0 0 1 3 4c0-.6.4-1 1-1h3.5c.6 0 1 .4 1 1 0 1.3.2 2.5.6 3.6.1.3 0 .7-.2 1z"/></svg>
        (044)-555-0192
      </li>
      <li class="contact">
        <svg viewBox="0 0 24 24" aria-hidden="true"><path d="M2 5h20v14H2z" /><path d="M2 5l10 8 10-8" fill="none" stroke="#fff" stroke-width="2"/></svg>
        curtis@ridgelinejourneys.com
      </li>
      <li class="contact">
        <svg viewBox="0 0 24 24" aria-hidden="true"><path d="M10 14a5 5 0 0 0 7 0l3-3a5 5 0 0 0-7-7l-1 1 1.4 1.4 1-1a3 3 0 0 1 4.2 4.2l-3 3a3 3 0 0 1-4.2 0zM14 10a5 5 0 0 0-7 0l-3 3a5 5 0 0 0 7 7l1-1-1.4-1.4-1 1a3 3 0 0 1-4.2-4.2l3-3a3 3 0 0 1 4.2 0z"/></svg>
        www.ridgelinejourneys.com
      </li>
    </ul>
  </section>

</main>
</body>
</html>
```